Brightway Haus Inc. Business Card Design

Brightway Haus Inc. is in search of a great clean design for our business cards!

Looking to incorporate our full logo and watermark on side one (however, I am open to having the text and watermark separated within the design.)

On side two, I am looking to have contact information (Name, Position, Phone #, Email, Website (www.thebrightwayhaus.ca). Can have the logo and/or watermark as part of the design if applicable.

Please add tagline "Where Shine Counts" on either side 1 or 2. This tagline can be in a sans serif, serif or cursive font as long as it compliments overall design. Capitalization can be title or sentence case depending on how it fits within the design.

Get creative!! Looking for a clean, crisp, premium design! Looking for a glossy card finish with spot UV features when printed. Cards will also be printed with rounded corners. Standard dimensions (3.5 x 2).

Target Market(s)

B2B - primary clients are business owners or property management corporations. (residential jobs are few and far between)

Industry/Entity Type

Business

Contact Information for Business Card

- clean, crisp design
- double sided
- spot UV accents and glossy finish upon printing
- standard business card size (3.5 x 2) with rounded corners
- please see project description for requirements per side

Font styles to use
Sans Serif

Requirements
Must have
• - adequate bleeds with print ready files
• - cohesive design elements between side 1 & 2
• - spot UV elements (can be on both sides or just one, use your discretion)
• - colour pallet should match the logo file provided
• - incorporate tagline "where shine counts" (this tagline can be in a serif or sans serif font as long as it is complimentary to the overall design.
Nice to have
• - Premium elements with a clean design
Should not have
• - Please omit cartoon or whimsical like designs, think premium.
• - Colours should not stray from the pallet of the provided logo.

```html
<!DOCTYPE html>
<html lang="en">
<head>
<meta charset="utf-8">
<title>Brightway Haus Inc. Business Card</title>
<link rel="stylesheet" href="https://fonts.googleapis.com/css2?family=Open+Sans:wght@700;800&family=Roboto:ital,wght@0,400;0,500;0,700;1,400&display=swap">
<style>
  :root {
    --teal: #0fb3b3;
    --navy: #1b2550;
    --paper: #f2f2f2;
    --shadow-grey: #a9a9a9;
    --backdrop: #2b2b2b;
    --white: #ffffff;
  }
  html, body {
    margin: 0;
    padding: 0;
    width: 1200px;
    height: 960px;
    overflow: hidden;
    background: var(--backdrop);
    font-family: "Roboto", Arial, sans-serif;
  }
  .stage { position: relative; width: 1200px; height: 960px; }
  .card {
    position: absolute;
    width: 600px;
    height: 343px;
    border-radius: 22px;
    overflow: hidden;
  }
  .card--front { left: 314px; top: 113px; background: var(--paper); }
  .card--back { left: 311px; top: 473px; background: var(--navy); }
  .card__wave { position: absolute; inset: 0; }
  .wordmark {
    position: absolute;
    font-family: "Open Sans", Arial, sans-serif;
    font-weight: 800;
    letter-spacing: -0.5px;
    white-space: nowrap;
    margin: 0;
  }
  .card--front .wordmark { left: 43px; top: 44px; font-size: 29px; color: var(--navy); }
  .card--back .wordmark {
    left: 0; right: 0; top: 144px; text-align: center;
    font-size: 36px; color: var(--white);
  }
  .holder { position: absolute; left: 44px; top: 114px; }
  .holder__name { margin: 0; font-size: 20px; font-weight: 500; color: var(--teal); letter-spacing: 0.3px; }
  .holder__role { margin: 4px 0 0; font-size: 14px; font-weight: 700; color: var(--navy); }
  .contact {
    position: absolute;
    right: 32px;
    top: 168px;
    color: var(--white);
    font-size: 14.5px;
    text-align: right;
    line-height: 19.5px;
  }
  .contact__address { margin: 0 0 10px; font-style: normal; }
  .contact__list { list-style: none; margin: 0; padding: 0; }
  .contact__item { display: flex; justify-content: flex-end; align-items: center; gap: 8px; }
  .contact__icon { width: 14px; height: 14px; fill: var(--white); flex: none; }
  .tagline {
    position: absolute;
    left: 0; right: 0; top: 274px;
    display: flex; align-items: center; justify-content: center; gap: 4px;
    color: var(--white);
    font-size: 19px;
    font-style: italic;
    margin: 0;
  }
  .tagline__rule {
    width: 115px; height: 1px;
    background: linear-gradient(90deg, rgba(255,255,255,0), rgba(255,255,255,0.8));
  }
  .tagline__rule--right {
    background: linear-gradient(90deg, rgba(255,255,255,0.8), rgba(255,255,255,0));
  }
  .tagline__accent { color: var(--teal); }
</style>
</head>
<body>
<main class="stage">

  <section class="card card--front" aria-label="Card front">
    <svg class="card__wave" viewBox="0 0 600 343" aria-hidden="true">
      <path fill="var(--shadow-grey)" transform="translate(-10,-12)" d="M0,250 C100,300 220,310 300,220 C380,120 440,20 570,0 L620,0 L620,360 L0,360 Z"/>
      <path fill="var(--navy)" transform="translate(-2,-7)" d="M0,250 C100,300 220,310 300,220 C380,120 440,20 570,0 L620,0 L620,360 L0,360 Z"/>
      <path fill="var(--teal)" stroke="var(--white)" stroke-width="2" d="M0,250 C100,300 220,310 300,220 C380,120 440,20 570,0 L620,0 L620,360 L0,360 Z" transform="translate(0,6)"/>
    </svg>

    <p class="wordmark">BRIGHTWAY HAUS INC.</p>

    <div class="holder">
      <h1 class="holder__name">MARA ELLISON</h1>
      <p class="holder__role">CEO/FOUNDER</p>
    </div>

    <div class="contact">
      <address class="contact__address">2140 Harbour Crest Road<br>Halifax, Nova Scotia 48210</address>
      <ul class="contact__list">
        <li class="contact__item">902 555 0148
          <svg class="contact__icon" viewBox="0 0 16 16" aria-hidden="true"><path d="M3.5 1 6 4 4.6 5.8c.8 2 2.6 3.8 4.6 4.6L11 9l3 2.5-1.5 2.8C7 14 2 9 1.7 3.5Z"/></svg>
        </li>
        <li class="contact__item">902 555 0173
          <svg class="contact__icon" viewBox="0 0 16 16" aria-hidden="true"><path d="M4.5 0h7A1.5 1.5 0 0 1 13 1.5v13a1.5 1.5 0 0 1-1.5 1.5h-7A1.5 1.5 0 0 1 3 14.5v-13A1.5 1.5 0 0 1 4.5 0Zm.5 2v10h6V2Zm3 11a1 1 0 1 0 0 2 1 1 0 0 0 0-2Z"/></svg>
        </li>
        <li class="contact__item">902 555 0196
          <svg class="contact__icon" viewBox="0 0 16 16" aria-hidden="true"><path d="M4 1h8v4H4Zm-3 5h14v6h-3v3H4v-3H1Zm4 5v3h6v-3Z"/></svg>
        </li>
        <li class="contact__item">hello@thebrightwayhaus.ca
          <svg class="contact__icon" viewBox="0 0 16 16" aria-hidden="true"><path d="M1 3h14v1.2L8 9 1 4.2Zm0 2.6 7 4.8 7-4.8V13H1Z"/></svg>
        </li>
        <li class="contact__item">www.thebrightwayhaus.ca
          <svg class="contact__icon" viewBox="0 0 16 16" aria-hidden="true"><circle cx="8" cy="8" r="7"/><path fill="var(--teal)" d="M5 4c1 0 2 1 1.5 2S4 7 4.5 8.5 6 10 6 12c-1.5-.5-3-2-3-4 0-2 1-3.5 2-4Zm5 2c1 0 2 .5 2.5 1.5S12 10 11 10.5 9 9 9.5 8 9 6 10 6Z"/></svg>
        </li>
      </ul>
    </div>
  </section>

  <section class="card card--back" aria-label="Card back">
    <p class="wordmark">BRIGHTWAY HAUS INC.</p>
    <p class="tagline">
      <span class="tagline__rule"></span>
      <span>Where <span class="tagline__accent">Shine</span> Counts</span>
      <span class="tagline__rule tagline__rule--right"></span>
    </p>
  </section>

</main>
</body>
</html>
```